Building company buisness cards

We are looking for a sharp modern new look for our business cards.
We are a New Zealand based company that specialises in house and land packages.
We have attached a photo of the current logo and would like to see if it can be improved somehow if needed.
We are open to any colours but we have chosen green at this stage.
Feel free to change the font and make the logo smarter looking.
Play with the colours and see what looks best.

We want a card that looks so good know one will want to throw it away!

Target Market(s)

Home buyers

Industry/Entity Type

Building

Contact Information for Business Card

Derek Tolvane
0217394062
dtolvane@quillmarkhomesteads.co.nz
quillmarkhomesteads.co.nz

Font styles to use
Serif
Sans Serif

Colors

Designer to choose colors to be used in the design.

Requirements
Must have
• Logo and company name on one side, details on the other side
Nice to have
• Color codes for the original green are HEX #4a8028, RGB(74,128,40), CMYK(42,0,69,50)
• Round corners, Raised and/or spot UV

```html
<!DOCTYPE html>
<html lang="en">
<head>
<meta charset="utf-8">
<title>Quillmark Homesteads – Business Cards</title>
<link rel="stylesheet" href="https://fonts.googleapis.com/css2?family=Montserrat:wght@400;500;700;800&display=swap">
<style>
  :root {
    --brand-green: #4a8028;
    --brand-green-bright: #3f9a34;
    --card-black: #1b1b1b;
    --card-white: #ffffff;
    --band-grey: #b3b3b3;
    --ink: #333333;
    --backdrop: #e4e4e4;
  }
  * { box-sizing: border-box; margin: 0; padding: 0; }
  html, body {
    width: 1200px; height: 900px; overflow: hidden;
    background: var(--backdrop);
    font-family: "Montserrat", sans-serif;
  }
  .canvas {
    width: 1200px; height: 900px;
    display: flex; flex-direction: column;
    align-items: center; justify-content: center; gap: 44px;
  }
  .card {
    position: relative;
    width: 640px; height: 366px;
    border-radius: 26px;
    overflow: hidden;
    box-shadow: 0 10px 24px rgba(0,0,0,0.18);
  }
  .card--back {
    background: var(--card-black);
    display: flex; align-items: center; justify-content: center;
  }
  .card--front { background: var(--card-white); }

  .wordmark {
    color: var(--brand-green-bright);
    font-weight: 800;
    line-height: 0.92;
    text-transform: lowercase;
    display: flex; flex-direction: column; align-items: center;
  }
  .wordmark__mark {
    width: 16px; height: 16px; border-radius: 50%;
    background: var(--brand-green-bright);
    margin-bottom: 10px;
  }
  .card--back .wordmark__top { font-size: 30px; }
  .card--back .wordmark__bottom { font-size: 44px; }

  .card--front .wordmark {
    position: absolute; left: 36px; top: 34px;
  }
  .card--front .wordmark__mark { width: 12px; height: 12px; margin-bottom: 7px; }
  .card--front .wordmark__top { font-size: 20px; }
  .card--front .wordmark__bottom { font-size: 29px; }

  .wave { position: absolute; left: 0; top: 0; width: 640px; height: 366px; }

  .contact {
    position: absolute; left: 280px; top: 146px;
    width: 330px;
    color: var(--ink);
  }
  .contact__name {
    color: var(--brand-green);
    font-weight: 700; font-size: 23px; line-height: 1.1;
  }
  .contact__role { font-size: 16px; font-weight: 400; margin-bottom: 12px; }
  .contact__list { list-style: none; font-size: 14px; line-height: 1.6; }
  .contact__item { display: flex; align-items: center; gap: 8px; white-space: nowrap; }
  .contact__icon { width: 13px; height: 13px; flex: none; }
</style>
</head>
<body>
<main class="canvas">

  <section class="card card--back" aria-label="Card back">
    <div class="wordmark">
      <span class="wordmark__mark"></span>
      <span class="wordmark__top">quillmark</span>
      <span class="wordmark__bottom">homesteads.</span>
    </div>
  </section>

  <section class="card card--front" aria-label="Card front">
    <div class="wordmark">
      <span class="wordmark__mark"></span>
      <span class="wordmark__top">quillmark</span>
      <span class="wordmark__bottom">homesteads.</span>
    </div>

    <svg class="wave" viewBox="0 0 640 366" aria-hidden="true">
      <path d="M0 250 C 200 258, 300 330, 450 342 C 540 349, 600 345, 640 338 L640 366 L0 366 Z" fill="var(--band-grey)"/>
      <path d="M0 259 C 200 267, 300 338, 450 349 C 540 355, 600 352, 640 348 L640 366 L0 366 Z" fill="var(--card-white)"/>
      <path d="M0 265 C 200 275, 300 345, 450 355 C 540 360, 600 358, 640 355 L640 366 L0 366 Z" fill="var(--brand-green)"/>
    </svg>

    <div class="contact">
      <p class="contact__name">Derek Tolvane</p>
      <p class="contact__role">Founder</p>
      <ul class="contact__list">
        <li class="contact__item">
          <svg class="contact__icon" viewBox="0 0 16 16" aria-hidden="true"><path d="M3 1.5 L6 1.5 L7 5 L5 6.5 C6 9 7.5 10.5 9.5 11 L11 9 L14.5 10 L14.5 13 C14.5 14 13.5 14.5 12.5 14.5 C6.5 14 2 9.5 1.5 3.5 C1.5 2.5 2 1.5 3 1.5 Z" fill="var(--brand-green)"/></svg>
          <span>0217394062</span>
        </li>
        <li class="contact__item">
          <svg class="contact__icon" viewBox="0 0 16 16" aria-hidden="true"><rect x="1.5" y="3.5" width="13" height="9" fill="none" stroke="var(--brand-green)" stroke-width="1.6"/><path d="M1.5 3.5 L8 9 L14.5 3.5" fill="none" stroke="var(--brand-green)" stroke-width="1.6"/></svg>
          <span>dtolvane@quillmarkhomesteads.co.nz</span>
        </li>
        <li class="contact__item">
          <svg class="contact__icon" viewBox="0 0 16 16" aria-hidden="true"><circle cx="8" cy="8" r="6.5" fill="none" stroke="var(--brand-green)" stroke-width="1.5"/><ellipse cx="8" cy="8" rx="2.8" ry="6.5" fill="none" stroke="var(--brand-green)" stroke-width="1.3"/><path d="M1.5 8 H14.5 M2.5 4.8 H13.5 M2.5 11.2 H13.5" stroke="var(--brand-green)" stroke-width="1.2"/></svg>
          <span>quillmarkhomesteads.co.nz</span>
        </li>
      </ul>
    </div>
  </section>

</main>
</body>
</html>
```